The Plate Compass

Cutting Through the Noise to What Actually Works.

Nutrition book

Target Market(s)

People looking to be or get healthy and eat right.

```html
<!DOCTYPE html>
<html lang="en">
<head>
<meta charset="utf-8">
<title>The Plate Compass — Book Cover</title>
<link href="https://fonts.googleapis.com/css2?family=Montserrat:wght@500;600;700;800&family=Poppins:wght@700;800&display=swap" rel="stylesheet">
<style>
  :root {
    --paper: #ffffff;
    --ink: #141414;
    --green-deep: #104c2b;
    --green: #2b7d3a;
    --rule-green: #1f5f31;
    --tear-grey: #e6e6e6;
    --tear-edge: #cfcfcf;
    --tier-supp: #c9c9c9;
    --tier-supp-edge: #7d7d7d;
    --tier-timing: #aecfda;
    --tier-timing-edge: #5e8f95;
    --tier-quality: #a7c878;
    --tier-quality-edge: #4f6b25;
    --tier-protein: #dca878;
    --tier-protein-edge: #6b3e1a;
    --tier-calories: #c2685b;
    --tier-calories-edge: #5e1f17;
  }
  * { margin: 0; padding: 0; box-sizing: border-box; }
  html, body { width: 800px; height: 1200px; overflow: hidden; background: var(--paper); }
  .cover { position: relative; width: 800px; height: 1200px; background: var(--paper); color: var(--ink); }

  .title { position: absolute; left: 0; width: 800px; text-align: center; font-family: "Montserrat", sans-serif; font-weight: 800; line-height: 1; }
  .title-the { top: 44px; font-size: 80px; letter-spacing: 1px; }
  .title-main {
    top: 130px; font-size: 124px; letter-spacing: -1px;
    background: linear-gradient(90deg, var(--green-deep) 20%, var(--green) 75%);
    -webkit-background-clip: text; background-clip: text; color: transparent;
  }
  .title-sub { top: 247px; font-size: 100px; letter-spacing: -1px; }

  .tagline {
    position: absolute; top: 358px; left: 0; width: 800px; text-align: center;
    font-family: "Montserrat", sans-serif; font-weight: 500; font-size: 23px;
  }
  .tagline strong { color: var(--green); font-weight: 700; }

  .pyramid { position: absolute; left: 0; top: 400px; width: 800px; height: 550px; }
  .tier-label { font-family: "Poppins", sans-serif; font-weight: 800; fill: var(--ink); }

  .noise-band { position: absolute; left: 0; top: 960px; width: 800px; height: 130px; }

  .author {
    position: absolute; top: 1118px; left: 0; width: 800px; height: 50px;
    display: flex; align-items: center; justify-content: center; gap: 28px;
  }
  .author-rule { width: 116px; height: 4px; background: var(--rule-green); }
  .author-name {
    font-family: "Montserrat", sans-serif; font-weight: 600; font-size: 44px;
    letter-spacing: 16px; margin-right: -16px; color: #222;
  }
</style>
</head>
<body>
<main class="cover">
  <h1>
    <span class="title title-the">THE</span>
    <span class="title title-main">PLATE</span>
    <span class="title title-sub">COMPASS</span>
  </h1>

  <p class="tagline">Cutting Through the Noise to <strong>What Actually Works.</strong></p>

  <svg class="pyramid" viewBox="0 400 800 550" xmlns="http://www.w3.org/2000/svg">
    <defs>
      <linearGradient id="supp-grad" x1="0" y1="0" x2="0" y2="1">
        <stop offset="0" stop-color="#d4d4d4"/><stop offset="1" stop-color="#b4b4b4"/>
      </linearGradient>
      <linearGradient id="timing-grad" x1="0" y1="0" x2="0" y2="1">
        <stop offset="0" stop-color="#b4d4de"/><stop offset="1" stop-color="#a2c7d2"/>
      </linearGradient>
      <linearGradient id="quality-grad" x1="0" y1="0" x2="0" y2="1">
        <stop offset="0" stop-color="#afcd7f"/><stop offset="1" stop-color="#97bb64"/>
      </linearGradient>
      <linearGradient id="protein-grad" x1="0" y1="0" x2="0" y2="1">
        <stop offset="0" stop-color="#e2b083"/><stop offset="1" stop-color="#d29a67"/>
      </linearGradient>
      <linearGradient id="calories-grad" x1="0" y1="0" x2="0" y2="1">
        <stop offset="0" stop-color="#c8705f"/><stop offset="1" stop-color="#b85c4e"/>
      </linearGradient>
    </defs>

    <!-- Supplements -->
    <g class="tier tier-supplements">
      <polygon points="406,412 475,528 335,528" fill="url(#supp-grad)"/>
      <polygon points="335,528 475,528 469,541 341,541" fill="var(--tier-supp-edge)"/>
      <ellipse role="img" aria-label="Two supplement capsules" cx="405" cy="472" rx="30" ry="16" fill="#c8a56a" transform="rotate(-20 405 472)"/>
      <text class="tier-label" x="406" y="523" font-size="15" text-anchor="middle">SUPPLEMENTS</text>
    </g>

    <!-- Meal timing -->
    <g class="tier tier-timing">
      <polygon points="305,542 482,542 523,623 287,623" fill="url(#timing-grad)"/>
      <polygon points="287,623 523,623 517,631 293,631" fill="var(--tier-timing-edge)"/>
      <ellipse role="img" aria-label="Alarm clock beside a fork" cx="365" cy="586" rx="42" ry="38" fill="#e9ecee"/>
      <text class="tier-label" x="455" y="582" font-size="19" text-anchor="middle">MEAL</text>
      <text class="tier-label" x="455" y="604" font-size="19" text-anchor="middle">TIMING</text>
    </g>

    <!-- Food quality -->
    <g class="tier tier-quality">
      <polygon points="278,633 530,633 572,719 237,719" fill="url(#quality-grad)"/>
      <polygon points="237,719 572,719 564,728 245,728" fill="var(--tier-quality-edge)"/>
      <ellipse role="img" aria-label="Kale, tomato, blueberries, avocado and salmon" cx="345" cy="678" rx="82" ry="34" fill="#6f8f45"/>
      <text class="tier-label" x="494" y="672" font-size="19" text-anchor="middle">FOOD</text>
      <text class="tier-label" x="494" y="695" font-size="19" text-anchor="middle">QUALITY</text>
    </g>

    <!-- Protein -->
    <g class="tier tier-protein">
      <polygon points="232,731 581,731 625,816 184,816" fill="url(#protein-grad)"/>
      <polygon points="184,816 625,816 617,827 193,827" fill="var(--tier-protein-edge)"/>
      <ellipse role="img" aria-label="Grilled chicken breast, boiled eggs and a bowl of sprouted lentils" cx="342" cy="775" rx="118" ry="34" fill="#e8cfae"/>
      <text class="tier-label" x="510" y="784" font-size="23" text-anchor="middle">PROTEIN</text>
    </g>

    <!-- Calories -->
    <g class="tier tier-calories">
      <polygon points="176,830 632,830 684,928 124,928" fill="url(#calories-grad)"/>
      <polygon points="124,928 684,928 675,940 134,940" fill="var(--tier-calories-edge)"/>
      <ellipse role="img" aria-label="Measuring tape beside a salad bowl with chicken, eggs and avocado" cx="320" cy="880" rx="112" ry="40" fill="#d9d2c4"/>
      <text class="tier-label" x="530" y="891" font-size="26" text-anchor="middle">CALORIES</text>
    </g>
  </svg>

  <svg class="noise-band" viewBox="0 960 800 130" xmlns="http://www.w3.org/2000/svg">
    <polygon fill="var(--tear-edge)" points="0,995 60,990 120,994 190,986 260,991 330,983 400,988 470,981 540,989 610,984 680,992 740,987 800,991 800,1056 740,1062 680,1058 610,1066 540,1060 470,1070 400,1064 330,1073 260,1066 190,1072 120,1064 60,1069 0,1062"/>
    <polygon fill="var(--tear-grey)" points="0,999 60,995 120,998 190,991 260,996 330,988 400,993 470,986 540,994 610,989 680,997 740,992 800,996 800,1052 740,1058 680,1054 610,1062 540,1056 470,1066 400,1060 330,1068 260,1062 190,1068 120,1060 60,1065 0,1058"/>
    <rect role="img" aria-label="Hand-lettered word noise, struck through" x="342" y="1008" width="152" height="36" rx="4" fill="#2a2a2a" opacity="0.85"/>
  </svg>

  <div class="author">
    <span class="author-rule"></span>
    <span class="author-name">MARCUS HALE</span>
    <span class="author-rule"></span>
  </div>
</main>
</body>
</html>
```